Design a label for a dog shampoo names fluffo, the sell point of this series of shampoo is “just like wash your dogs with milk, not harm for your hand ”, the style could be gentle or professional or even amazing.

Use only 2 colors in the design job, the color of our logo could be changed, it depends on your whole page. Please design in CDR or ai.

update:
Pls do more change with the fonts when you design the front page, including title and details. Try more styles of fonts. Addition, this design will be printed on the bottle, no a label stick on it.
Updates

Do not put a real dog or animal on the page, Pay more attention to the types of fonts

Reason: Expect for more design idea.

Target Market(s)

people 20-30 years old who have dogs and cats at home

Industry/Entity Type

It Professional

Requirements
Nice to have
• It would be nice if you add some detail words in the design of the right side.

```html
<!DOCTYPE html>
<html lang="en">
<head>
<meta charset="utf-8">
<title>Fluffo Super Conditioning Nutrient Shampoo</title>
<link rel="stylesheet" href="https://fonts.googleapis.com/css2?family=Fredoka:wght@400;600&display=swap">
<style>
  :root {
    --ink-deep: #3f6f9d;
    --ink-soft: #8fbad1;
    --surface: #f6f6f3;
    --paper: #ffffff;
  }
  * { margin: 0; padding: 0; box-sizing: border-box; }
  html, body {
    width: 1200px;
    height: 2495px;
    overflow: hidden;
    background: var(--surface);
  }
  .canvas {
    position: relative;
    width: 1200px;
    height: 2495px;
  }
  .label-art {
    position: absolute;
    left: 0;
    top: 0;
    width: 1200px;
    height: 2495px;
  }
  .brand-name {
    fill: var(--ink-soft);
    font-family: "Fredoka", sans-serif;
    font-weight: 600;
  }
  .brand-dot { fill: var(--ink-deep); }
  .claim {
    fill: var(--ink-deep);
    font-family: "Fredoka", sans-serif;
    font-weight: 600;
    font-size: 42px;
  }
  .product-band { fill: var(--ink-deep); }
  .product-name {
    fill: var(--paper);
    font-family: "Fredoka", sans-serif;
    font-weight: 400;
    font-size: 56px;
  }
  .pet-emblem {
    position: absolute;
    left: 462px;
    top: 1980px;
    width: 222px;
    height: 138px;
    border-radius: 69px;
    background: linear-gradient(90deg, var(--ink-soft) 0%, var(--ink-soft) 30%, var(--ink-deep) 60%, var(--ink-deep) 100%);
  }
</style>
</head>
<body>
<main class="canvas">
  <svg class="label-art" viewBox="0 0 1200 2495">
    <g class="brand-mark" aria-label="fluffo">
      <circle class="brand-dot" cx="268" cy="902" r="38"/>
      <text class="brand-name" x="210" y="1247" font-size="420" textLength="814" lengthAdjust="spacingAndGlyphs">FLUF</text>
      <text class="brand-name" x="609" y="1560" font-size="340" textLength="384" lengthAdjust="spacingAndGlyphs">FO</text>
    </g>

    <g class="claims">
      <text class="claim" x="551" y="1370" text-anchor="end">moisture rich</text>
      <text class="claim" x="551" y="1450" text-anchor="end">smooth &amp; silky</text>
      <text class="claim" x="551" y="1528" text-anchor="end">1000ml</text>
    </g>

    <rect class="product-band" x="218" y="1641" width="780" height="244" rx="50"/>
    <text class="product-name" x="297" y="1752" textLength="635" lengthAdjust="spacing">super conditioning</text>
    <text class="product-name" x="310" y="1832" textLength="609" lengthAdjust="spacing">nutrient shampoo</text>
  </svg>

  <div class="pet-emblem" role="img" aria-label="Small emblem of a dog surrounded by bubbles"></div>
</main>
</body>
</html>
```